Boat Detail Postcard Design

We are looking for a postcard design for a boat detailing company called "Harlow Gleam Detailing" in Coral Inlet, Gulf Coast. It is a veteran owned small business. We make sure to give customers a show room finish that is inspection ready the, first time, every time. Our services include: deep clean, compound & wax, bottom scrapping,and satisfaction guaranteed. We would like to incorporate garnet as the color for the company name and water droplets or water and we would like to maintain a professional appearance.

Target Market(s)

ages 25-75 that own boats and are of upper or upper middle class

Industry/Entity Type

Business

```html
<!DOCTYPE html>
<html lang="en">
<head>
<meta charset="utf-8">
<title>Harlow Gleam Detailing – Postcard Back</title>
<link href="https://fonts.googleapis.com/css2?family=Open+Sans:wght@400;700&family=PT+Sans+Narrow:wght@400;700&display=swap" rel="stylesheet">
<style>
  :root {
    --garnet: #7a2a24;
    --white: #ffffff;
    --ink: #111111;
    --rule: #8c8c8c;
  }
  html, body {
    margin: 0;
    padding: 0;
    width: 1200px;
    height: 930px;
    overflow: hidden;
    background: var(--white);
  }
  .postcard {
    position: relative;
    width: 1200px;
    height: 930px;
    overflow: hidden;
    background: var(--white);
  }
  .postcard__art {
    position: absolute;
    inset: 0;
  }
  .headline {
    position: absolute;
    left: 60px;
    top: 56px;
    width: 800px;
    margin: 0;
    font-family: "Open Sans", Arial, sans-serif;
    font-weight: 700;
    font-size: 39px;
    line-height: 49px;
    color: var(--white);
    white-space: nowrap;
  }
  .intro {
    position: absolute;
    left: 62px;
    top: 222px;
    width: 480px;
    margin: 0;
    font-family: "Open Sans", Arial, sans-serif;
    font-size: 28.5px;
    line-height: 32.7px;
    color: var(--white);
    white-space: nowrap;
  }
  .contact {
    position: absolute;
    left: 63px;
    top: 476px;
    margin: 0;
    font-family: "PT Sans Narrow", "Arial Narrow", sans-serif;
    font-size: 26px;
    line-height: 33px;
    color: var(--white);
    font-style: normal;
  }
  .contact__phone {
    margin-top: 15px;
  }
  .contact__label {
    display: block;
    font-weight: 700;
  }
  .website {
    position: absolute;
    left: 28px;
    top: 843px;
    margin: 0;
    font-family: "PT Sans Narrow", "Arial Narrow", sans-serif;
    font-weight: 700;
    font-size: 41px;
    line-height: 1;
    color: var(--ink);
  }
  .stamp-box {
    position: absolute;
    left: 997px;
    top: 63px;
    width: 125px;
    height: 143px;
    border: 1.5px solid var(--rule);
    box-sizing: border-box;
  }
  .address-lines {
    position: absolute;
    left: 676px;
    top: 484px;
    width: 416px;
  }
  .address-lines span {
    display: block;
    height: 52px;
    border-top: 1.5px solid var(--rule);
  }
</style>
</head>
<body>
<main class="postcard">
  <svg class="postcard__art" width="1200" height="930" viewBox="0 0 1200 930">
    <defs>
      <linearGradient id="garnetPhoto" x1="0" y1="0" x2="1" y2="1">
        <stop offset="0" stop-color="#7e2f28"/>
        <stop offset="0.5" stop-color="#8c3b33"/>
        <stop offset="1" stop-color="#6e2520"/>
      </linearGradient>
      <linearGradient id="waterSplash" x1="0" y1="0" x2="1" y2="0.4">
        <stop offset="0" stop-color="#4a4a4a"/>
        <stop offset="0.45" stop-color="#9a9a9a"/>
        <stop offset="1" stop-color="#ffffff"/>
      </linearGradient>
      <linearGradient id="waterFloor" x1="0" y1="0" x2="0" y2="1">
        <stop offset="0" stop-color="#555555" stop-opacity="0.9"/>
        <stop offset="0.35" stop-color="#c9c9c9"/>
        <stop offset="1" stop-color="#dedede"/>
      </linearGradient>
    </defs>
    <path role="img" aria-label="Photo of detailed boats on trailers, tinted garnet"
          d="M0 0 H911 V230 H748 C620 230 522 330 522 432 V930 H0 Z"
          fill="url(#garnetPhoto)"/>
    <path role="img" aria-label="Photo of splashing water across the bottom of the card"
          d="M0 640 C120 660 240 700 340 695 C420 690 470 720 560 730 C700 745 820 790 960 810 C1060 825 1140 850 1200 860 V930 H0 Z"
          fill="url(#waterSplash)"/>
    <path d="M0 700 C160 720 320 760 520 790 C680 815 760 860 760 930 H0 Z"
          fill="url(#waterFloor)" opacity="0.85"/>
  </svg>

  <h1 class="headline">Sed ut perspiciatis unde omnis iste<br>natus error sit voluptatem accusan-<br>tium doloremque laudantium.</h1>

  <p class="intro">Lorem ipsum dolor sit amet,<br>consectetur adipiscing elit, sed<br>do eiusmod tempor incididunt<br>ut labore et dolore magna<br>aliqua. Ut enim ad minim<br>veniam, quis nostrud<br>exercitation ullamco laboris.</p>

  <address class="contact">
    <div class="contact__street">Harlow Gleam Detail’s Address<br>Coral Inlet, Gulf Coast</div>
    <div class="contact__phone"><span class="contact__label">Toll Free:</span>1 (123) 456-7890</div>
  </address>

  <p class="website">www.harlowgleamdetailing.com</p>

  <div class="stamp-box" aria-label="Stamp area"></div>

  <div class="address-lines" aria-label="Mailing address lines">
    <span></span><span></span><span></span><span></span>
  </div>
</main>
</body>
</html>
```